Business Card Design For Office Furniture Clearance Company

Kestrel Office Clearance - our company name pretty much explains what we do, we clear offices for high end clients, mainly plc's and large international companies.

We require a nice looking business card that displays professionalism but without being too serious.

It would be nice to see just a little more than a conventional boring business card, make sure you add some flare.

Industry/Entity Type

Office Furniture

Contact Information for Business Card

CARD 1

Mark Holloway
Director
mark@kestrelofficeclearance.co.uk
m: 07700 153928

t: 01632 960418
www.kestrelofficeclearance.co.uk

Kestrel Office Clearance
Unit K4 B
2-8 Fenwick Lane
Harwick
Stonebridge Vale
ZZ9 4QT

zero-cost office clearances… hard to beat a deal like that.

CARD 2

Peter Radford
Director
peter@kestrelofficeclearance.co.uk
m: 07700 382615

t: 01632 960418

Kestrel Office Clearance
Unit K4 B
2-8 Fenwick Lane
Harwick
Stonebridge Vale
ZZ9 4QT

Font styles to use
Sans Serif

Requirements
Must have
• A white background - as we have a blue logo.
Nice to have
• Nice use of the logo - play around with this and dissect it.

```html
<!DOCTYPE html>
<html lang="en">
<head>
<meta charset="utf-8">
<title>Kestrel Office Clearance – Business Cards</title>
<link rel="stylesheet" href="https://fonts.googleapis.com/css2?family=Open+Sans:wght@400;600&display=swap">
<style>
  :root {
    --stage: #e9e6e1;
    --card: #ffffff;
    --card-shade: #eceff1;
    --brand-blue: #1a7fc4;
    --brand-blue-light: #3b9ad6;
    --brand-blue-deep: #136aa7;
    --text-grey: #4a4d50;
    --text-soft: #6b6f73;
  }
  * { box-sizing: border-box; margin: 0; padding: 0; }
  html, body {
    width: 1200px; height: 843px; overflow: hidden;
    background: var(--stage);
    font-family: "Open Sans", Arial, sans-serif;
  }
  .stage { position: relative; width: 1200px; height: 843px; }

  .card {
    position: absolute;
    width: 540px; height: 310px;
    background: linear-gradient(160deg, var(--card) 55%, var(--card-shade) 100%);
    box-shadow: 0 10px 28px rgba(0,0,0,0.22);
    overflow: hidden;
  }

  /* Card back */
  .card--back { left: 70px; top: 110px; }
  .card--back .brand-disc {
    position: absolute; left: 28px; top: 40px;
    width: 230px; height: 230px; border-radius: 50%;
    background: radial-gradient(circle at 40% 35%, var(--brand-blue-light), var(--brand-blue) 70%);
  }
  .card--back .brand-block {
    position: absolute; left: 276px; top: 132px; width: 250px;
  }
  .brand-name {
    color: var(--brand-blue); font-weight: 600; font-size: 19px; line-height: 1.2;
  }
  .tagline {
    margin-top: 6px; color: var(--text-soft); font-size: 13px; line-height: 1.35;
  }

  /* Card front */
  .card--front { left: 600px; top: 440px; }
  .card--front .band {
    position: absolute; left: 0; top: 0; width: 200px; height: 100%;
    background: linear-gradient(180deg, var(--brand-blue-light), var(--brand-blue-deep));
  }
  .card--front .band-disc {
    position: absolute; left: 105px; top: 70px;
    width: 170px; height: 170px; border-radius: 50%;
    background: var(--brand-blue);
    border: 2px solid rgba(255,255,255,0.85);
  }
  .details {
    position: absolute; left: 300px; top: 52px; width: 236px;
    color: var(--text-grey); font-size: 12.5px; line-height: 1.45;
  }
  .person-name { color: var(--brand-blue); font-size: 20px; font-weight: 400; line-height: 1.1; }
  .person-role { color: var(--text-grey); font-size: 13px; margin-bottom: 10px; }
  .company { color: var(--brand-blue); font-weight: 600; font-size: 13px; }
  .address { margin-bottom: 8px; }
  .contact-list { list-style: none; }
  .contact-list li { display: flex; align-items: center; gap: 7px; white-space: nowrap; }
  .contact-list svg { width: 12px; height: 12px; flex: none; fill: var(--brand-blue); }
</style>
</head>
<body>
<main class="stage">

  <section class="card card--back" aria-label="Card back">
    <div class="brand-disc"></div>
    <div class="brand-block">
      <p class="brand-name">Kestrel Office Clearance</p>
      <p class="tagline">zero-cost office clearances…<br>hard to beat a deal like that.</p>
    </div>
  </section>

  <section class="card card--front" aria-label="Card front">
    <div class="band"></div>
    <div class="band-disc"></div>
    <div class="details">
      <p class="person-name">Mark Holloway</p>
      <p class="person-role">Director</p>
      <p class="company">Kestrel Office Clearance</p>
      <p class="address">Unit K4 B, 2-8 Fenwick Lane<br>Harwick, Stonebridge Vale, ZZ9 4QT</p>
      <ul class="contact-list">
        <li><svg viewBox="0 0 24 24" aria-hidden="true"><path d="M6.6 10.8a15 15 0 0 0 6.6 6.6l2.2-2.2a1 1 0 0 1 1-.25 11.4 11.4 0 0 0 3.6.57 1 1 0 0 1 1 1V20a1 1 0 0 1-1 1A17 17 0 0 1 3 4a1 1 0 0 1 1-1h3.5a1 1 0 0 1 1 1c0 1.25.2 2.45.57 3.57a1 1 0 0 1-.25 1z"/></svg>01632 960418</li>
        <li><svg viewBox="0 0 24 24" aria-hidden="true"><path d="M7 1h10a2 2 0 0 1 2 2v18a2 2 0 0 1-2 2H7a2 2 0 0 1-2-2V3a2 2 0 0 1 2-2zm0 3v14h10V4zm5 15.5a1 1 0 1 0 0 2 1 1 0 0 0 0-2z"/></svg>07700 153928</li>
        <li><svg viewBox="0 0 24 24" aria-hidden="true"><path d="M2 5h20v14H2zm2 2v.5l8 5 8-5V7zm0 2.9V17h16V9.9l-8 5z"/></svg>mark@kestrelofficeclearance.co.uk</li>
        <li><svg viewBox="0 0 24 24" aria-hidden="true"><path d="M12 2a10 10 0 1 0 0 20 10 10 0 0 0 0-20zm6.9 9h-3a15 15 0 0 0-1.3-5.6A8 8 0 0 1 18.9 11zM12 4.1c.9 1.2 1.8 3.6 1.9 6.9h-3.8c.1-3.3 1-5.7 1.9-6.9zM9.4 5.4A15 15 0 0 0 8.1 11h-3a8 8 0 0 1 4.3-5.6zM5.1 13h3a15 15 0 0 0 1.3 5.6A8 8 0 0 1 5.1 13zm6.9 6.9c-.9-1.2-1.8-3.6-1.9-6.9h3.8c-.1 3.3-1 5.7-1.9 6.9zm2.6-1.3a15 15 0 0 0 1.3-5.6h3a8 8 0 0 1-4.3 5.6z"/></svg>www.kestrelofficeclearance.co.uk</li>
      </ul>
    </div>
  </section>

</main>
</body>
</html>
```